Package Design - Disposable Face Towel

Hi,

We are needing assistance with graphic design on our box/carton/package.

The attached image that is white is our biggest competitor.

Our brand is "VELMORA BATH CO." Please see the logo we uploaded.

Oder we have in mind for front of box:

Logo
LARGE TOWELS
50 Count
Ultra Soft| 100% USDA Bio-Based|100% Eucalyptus Viscose | Vegan
VELMORABATHCO.COM

We like medium to dark blue on most of the box, with white and minimal hot pink or salmon. Something that is sharp, modern, and stands out from our competitors.

Box dimensions are: 6.25 x 5.25 x 4.75 inches

This will be 1 of many design projects.

Target Market(s)

Female Beauty Products

Font styles to use
Serif
Sans Serif

Colors
0054AA
0677BA
7BADD7
CADEEF
E8F1F8
EB3D1F
EC4F4E
F09395
F8D3D4
FCEDEE

Requirements
Must have
• Needs to look sharp and modern

```html
<!DOCTYPE html>
<html lang="en">
<head>
<meta charset="utf-8">
<title>Velmora Bath Co. – Large Towel Carton</title>
<link rel="stylesheet" href="https://fonts.googleapis.com/css2?family=Raleway:wght@300;400&family=Roboto+Condensed:wght@300;400;700&display=swap">
<style>
  :root{
    --bg:#e3e3e3;
    --blue-deep:#0054aa;
    --blue:#0677ba;
    --sky:#7badd7;
    --ice:#cadeef;
    --mist:#e8f1f8;
    --white:#ffffff;
    --pink:#ec4f4e;
    --blush:#f09395;
  }
  *{box-sizing:border-box;margin:0;padding:0}
  html,body{width:870px;height:1200px;overflow:hidden;background:var(--bg)}
  .canvas{position:relative;width:870px;height:1200px}

  .panel{position:absolute;overflow:hidden}
  .brand-name{font-family:"Raleway",sans-serif;font-weight:400;letter-spacing:.04em;text-transform:uppercase;line-height:1.15;text-align:center}

  /* top flap */
  .panel-top{left:450px;top:230px;width:380px;height:300px;background:var(--blue-deep)}
  .panel-top .opening{position:absolute;inset:0}
  .top-label{position:absolute;left:60px;top:70px;width:260px;height:80px;background:var(--ice);
    display:flex;align-items:center;justify-content:center}
  .top-label .brand-name{color:var(--blue-deep);font-size:21px}

  /* front face */
  .panel-front{left:450px;top:550px;width:380px;height:420px;background:var(--ice)}
  .front-band{position:absolute;left:0;right:0;top:228px;height:142px;background:var(--blue-deep)}
  .front-lines{position:absolute;inset:0}
  .logo-block{position:absolute;left:115px;top:82px;width:150px;height:76px;background:var(--blue-deep);
    display:flex;align-items:center;justify-content:center;padding:0 10px}
  .logo-block .brand-name{color:var(--white);font-size:16px}
  .product-name{position:absolute;left:0;right:0;top:288px;text-align:center;
    font-family:"Raleway",sans-serif;font-weight:300;font-size:34px;line-height:1.2;color:var(--white);letter-spacing:-.01em}
  .product-count{position:absolute;left:0;right:0;top:336px;text-align:center;
    font-family:"Roboto Condensed",sans-serif;font-weight:700;font-size:14px;line-height:1.2;color:var(--blush);letter-spacing:.03em}
  .front-strip{position:absolute;left:0;right:0;top:370px;height:50px;background:var(--ice);
    display:flex;flex-direction:column;align-items:center;justify-content:center;gap:3px;
    font-family:"Roboto Condensed",sans-serif;color:var(--blue-deep)}
  .features{font-weight:400;font-size:11.5px;letter-spacing:.02em}
  .website{font-weight:700;font-size:11px;letter-spacing:.08em;color:var(--pink)}

  /* side face */
  .panel-side{left:40px;top:550px;width:390px;height:420px;background:var(--ice)}
  .side-band{position:absolute;left:0;right:0;top:232px;bottom:0;background:var(--blue-deep)}
  .info-card{position:absolute;left:36px;top:30px;width:318px;height:362px;background:var(--mist);
    clip-path:polygon(6% 0,94% 0,100% 5%,100% 95%,94% 100%,6% 100%,0 95%,0 5%);
    padding:34px 30px 20px 30px}
  .info-title{font-family:"Roboto Condensed",sans-serif;font-weight:700;font-size:13px;color:var(--pink);
    text-transform:uppercase;margin-bottom:12px;letter-spacing:.02em}
  .info-body{font-family:"Roboto Condensed",sans-serif;font-weight:300;font-size:12.5px;line-height:1.45;
    color:var(--blue-deep);text-align:justify}
</style>
</head>
<body>
<main class="canvas">

  <section class="panel panel-top" aria-label="Top flap">
    <svg class="opening" width="380" height="300" viewBox="0 0 380 300" aria-hidden="true">
      <rect x="50" y="190" width="280" height="60" rx="22" fill="none" stroke="#7badd7" stroke-width="1.2" stroke-dasharray="6 5"/>
    </svg>
    <div class="top-label"><span class="brand-name">Velmora Bath Co.</span></div>
  </section>

  <section class="panel panel-side" aria-label="Side panel">
    <div class="side-band"></div>
    <article class="info-card">
      <h2 class="info-title">Why Velmora Bath Towels</h2>
      <p class="info-body">Using clean skin towels is crucial for maintaining healthy and clear skin. Firstly, clean towels help prevent the spread of bacteria, which can cause acne and other skin infections. Secondly, they remove excess oil, dirt, and dead skin cells without reintroducing impurities back onto your skin. Thirdly, clean towels are gentler and less abrasive, reducing the risk of irritation and inflammation. Additionally, using a fresh towel ensures that skincare products are more effectively absorbed, enhancing their benefits. Lastly, maintaining clean towels as part of your skincare routine promotes overall hygiene and fosters a healthier complexion.</p>
    </article>
  </section>

  <section class="panel panel-front" aria-label="Front panel">
    <div class="front-band"></div>
    <svg class="front-lines" width="380" height="420" viewBox="0 0 380 420" aria-hidden="true">
      <line x1="48" y1="0" x2="48" y2="228" stroke="#7badd7" stroke-width="1" stroke-dasharray="6 5"/>
      <line x1="332" y1="0" x2="332" y2="228" stroke="#7badd7" stroke-width="1" stroke-dasharray="6 5"/>
      <rect x="40" y="236" width="300" height="48" rx="18" fill="none" stroke="#7badd7" stroke-width="1" stroke-dasharray="6 5"/>
    </svg>
    <div class="logo-block"><span class="brand-name">Velmora Bath<br>Co.</span></div>
    <h1 class="product-name">LARGE TOWEL</h1>
    <p class="product-count">50 COUNT</p>
    <div class="front-strip">
      <p class="features">ULTRA SOFT | 100% USDA BIO-BASED | 100% EUCALYPTUS VISCOSE | VEGAN</p>
      <p class="website">VELMORABATHCO.COM</p>
    </div>
  </section>

</main>
</body>
</html>
```